Homepage mockup for RoutineVerdict.com

I would like a homepage mockup of routineverdict.com.

Basically what the site does, is it allows a person to upload a video of a gymnastics routine and our certified judges will judge the routine providing a score, as well as provide a critique and feedback as to why they gave you that score. Many times people don't know why they got the score they did at a gymnastics competition, so this site aims to provide reasoning behind it.

I have started to design the homepage myself (see attached), and like it, but I'd like a professional to finish the layout, or even come up with something really wow and original. I like clean, typically simple design.

THIS IS AN OLD VERSION OF THE SITE (http://esite.kelpradia.com/) This should only be used so you can get an idea of what the site is about. I DO NOT want the new site to look like this, but the basic concept and content remains the same.

DESIGNER FILES CAN BE DOWNLOADED HERE (http://kelpradia.com/files.aspx)

Target Market(s)

Gymnastic type people, parents of gymnasts, coaches, etc.

Industry/Entity Type

It Professional

Requirements
Must have
• -Routine verdict logo (provided)
-Not required, but I have attached the main photo I used in my mockup (AI File)
*A step by step graphic(s) depicting the process for a user. A How it works sort of explanation. Should be eye catching, not just text.

-Step 1: Videotape your gymnastic routine.
-Step 2: Create an account and share us your video.
-Step 3: Our certified judges will score and critique your routine, fully explaining the reasons behind their score.

```html
<!DOCTYPE html>
<html lang="en">
<head>
<meta charset="utf-8">
<title>Routine verdict – Your Personal Gymnastic Judge</title>
<link href="https://fonts.googleapis.com/css2?family=Arimo:wght@400;700&family=Kalam:wght@400&family=Delius&display=swap" rel="stylesheet">
<style>
:root{
  --brand-blue:#1f7fc0;
  --brand-red:#a3232b;
  --deep-red:#8a1d22;
  --script-blue:#2a6fa8;
  --ink:#3a3a3a;
  --body-text:#6a6a6a;
  --stage-light:#f7f7f7;
  --stage-dark:#e2e2e2;
  --floor-light:#efe0d0;
  --floor-dark:#dcc3aa;
  --footer:#2b2b2b;
  --footer-text:#c9c9c9;
  --orange:#f08a12;
}
*{box-sizing:border-box;margin:0;padding:0}
html,body{width:1200px;height:680px;overflow:hidden}
body{font-family:"Arimo",Arial,sans-serif;background:var(--stage-dark)}
.page{position:relative;width:1200px;height:680px;overflow:hidden;
  background:radial-gradient(ellipse 520px 340px at 520px 330px,#fcfcfc 0%,var(--stage-light) 45%,var(--stage-dark) 100%)}
.site-header{position:absolute;left:0;top:0;width:1200px;height:92px;
  background:linear-gradient(#f4f6f8,#ffffff 40%,#eef1f4);border-bottom:3px solid #fff;box-shadow:0 1px 2px rgba(0,0,0,.08)}
.brand{position:absolute;left:210px;top:34px;display:flex;align-items:center;gap:8px;
  font-weight:700;font-size:26px;color:var(--brand-blue);letter-spacing:-.5px}
.brand-mark{width:18px;height:18px;background:var(--brand-blue);border-radius:3px}
.main-nav{position:absolute;left:482px;top:51px;display:flex;align-items:center;font-size:11px}
.main-nav a{color:var(--brand-red);text-decoration:none;margin-right:35px;line-height:23px}
.main-nav a.is-active{background:var(--brand-blue);color:#fff;padding:0 13px;border-radius:2px;margin-right:22px}
.main-nav a:last-child{margin-right:0}
.login-tab{position:absolute;left:859px;top:92px;width:131px;height:35px;background:linear-gradient(#fff,#f1f1f1);
  border-radius:0 0 10px 10px;box-shadow:0 1px 3px rgba(0,0,0,.2);display:flex;align-items:center;justify-content:center;gap:8px;
  font-size:11px;color:#666}
.score-card{position:absolute;background:#fbfbfb;box-shadow:1px 1px 4px rgba(0,0,0,.25);
  font-family:"Delius",Georgia,serif;color:#444;display:flex;align-items:center;justify-content:center}
.tagline{position:absolute;left:324px;font-family:"Kalam",cursive;font-size:22px;line-height:1}
.tagline-red{top:151px;color:var(--brand-red)}
.tagline-blue{top:184px;color:var(--script-blue)}
.tagline-blue b{font-family:"Arimo",sans-serif;font-weight:400;color:var(--ink);font-size:20px}
.cta-frame{position:absolute;left:327px;top:235px;width:208px;height:54px;border-radius:14px;background:linear-gradient(#ececec,#d8d8d8);box-shadow:inset 0 1px 2px rgba(0,0,0,.1)}
.cta-start{position:absolute;left:8px;top:8px;width:192px;height:38px;border-radius:9px;
  background:linear-gradient(#3f7ee0,#1e4fb8 55%,#1a3f9a);color:#fff;display:flex;align-items:center;padding:0 10px;gap:10px;box-shadow:0 1px 2px rgba(0,0,0,.3)}
.cta-start small{font-size:9.5px;line-height:10px;text-align:center;font-weight:700}
.cta-start strong{font-size:17px;font-weight:700;letter-spacing:-.3px}
.intro{position:absolute;left:219px;top:311px;width:380px;font-size:11px;line-height:17.6px;color:var(--body-text)}
.steps{position:absolute;left:200px;top:410px}
.hero-photo{position:absolute;left:590px;top:190px;width:410px;height:435px;
  background:radial-gradient(ellipse 40% 48% at 55% 45%,rgba(60,50,45,.55),rgba(200,180,165,.35) 60%,rgba(230,230,230,0) 100%)}
.promo{position:absolute;left:810px;top:438px;width:186px;text-align:center;font-size:19.5px;line-height:26px;color:var(--deep-red)}
.cta-member{position:absolute;left:827px;top:497px;width:156px;height:29px;border-radius:15px;
  background:linear-gradient(#d8463e,#a8201c);color:#fff;font-size:11.5px;font-weight:700;display:flex;align-items:center;justify-content:center;gap:10px;
  box-shadow:0 0 0 2px #f1f1f1,0 1px 4px rgba(0,0,0,.35)}
.cta-member i{width:13px;height:13px;border-radius:50%;background:#3a0c0c;position:relative}
.cta-member i:after{content:"";position:absolute;left:5px;top:3.5px;border-left:4px solid #fff;border-top:3px solid transparent;border-bottom:3px solid transparent}
.floor{position:absolute;left:0;top:590px;width:1200px;height:57px;background:linear-gradient(var(--floor-dark),var(--floor-light) 35%,#e8d2bd)}
.blog-link{position:absolute;left:208px;top:613px;display:flex;align-items:center;gap:5px}
.rss{width:12px;height:12px;background:var(--orange);border-radius:2px}
.blog-link span{background:linear-gradient(#f7a126,#ec7a0b);color:#fff;font-family:Georgia,serif;font-size:11px;padding:3px 6px;border-radius:2px}
.social{position:absolute;left:889px;top:611px;display:flex;gap:7px}
.social span{width:20px;height:20px;border-radius:50%;background:#4a4a4a;box-shadow:0 0 0 1px #fff inset;display:flex;align-items:center;justify-content:center}
.site-footer{position:absolute;left:0;top:647px;width:1200px;height:33px;background:var(--footer);color:var(--footer-text);
  font-size:10px;text-align:center;line-height:33px}
</style>
</head>
<body>
<div class="page">
  <header class="site-header">
    <div class="brand"><span class="brand-mark"></span>Routine verdict</div>
    <nav class="main-nav">
      <a class="is-active" href="#">Home</a>
      <a href="#">About us</a>
      <a href="#">How it works</a>
      <a href="#">Sample</a>
      <a href="#">Members Area</a>
      <a href="#">Contact</a>
      <a href="#">FAQ</a>
    </nav>
  </header>
  <div class="login-tab">
    <svg width="16" height="20" viewBox="0 0 16 20"><path d="M4 9V6a4 4 0 0 1 8 0v3" fill="none" stroke="#777" stroke-width="2"/><rect x="1" y="9" width="14" height="10" rx="2" fill="#8a8a8a"/></svg>
    Memeber Login
  </div>

  <div class="score-card" style="left:263px;top:150px;width:49px;height:73px;font-size:32px">5</div>
  <div class="score-card" style="left:220px;top:174px;width:50px;height:73px;font-size:32px">1</div>
  <div class="score-card" style="left:255px;top:215px;width:50px;height:74px;font-size:32px">10</div>

  <p class="tagline tagline-red">Judges only give you a number....</p>
  <p class="tagline tagline-blue">...We explain the reason <b>WHY</b></p>

  <div class="cta-frame">
    <a class="cta-start"><small>Upload your video<br>&amp; get critiqued!</small><strong>Get started</strong></a>
  </div>

  <p class="intro">Registration is FREE and only takes a minute, donec et ligula elit, vel consectetur sem. Nunc semper congue suscipit. Mauris nibh massa, scelerisque in placerat aliquam, pretium a orci. Phasellus sit amet nulla sit amet erat placerat porta sed posuere ipsum.</p>

  <svg class="steps" width="440" height="140" viewBox="200 410 440 140" aria-label="How it works: three steps">
    <defs>
      <radialGradient id="disc" cx="50%" cy="40%" r="60%"><stop offset="0" stop-color="#fafafa"/><stop offset="1" stop-color="#e2e2e2"/></radialGradient>
      <path id="arc1" d="M213 468 A58 58 0 0 1 328 470"/>
      <path id="arc2" d="M366 462 A58 58 0 0 1 480 470"/>
      <path id="arc3" d="M533 445 A58 58 0 0 1 626 445"/>
    </defs>
    <g font-family="Delius, sans-serif" font-size="15" fill="#777">
      <text><textPath href="#arc1">Record your Routine</textPath></text>
      <text><textPath href="#arc2">Sign up and Upload</textPath></text>
      <text><textPath href="#arc3">Get the “Why”</textPath></text>
    </g>
    <g filter="none">
      <circle cx="268" cy="487" r="50" fill="url(#disc)" stroke="#fff" stroke-width="3"/>
      <circle cx="421" cy="487" r="50" fill="url(#disc)" stroke="#fff" stroke-width="3"/>
      <circle cx="573" cy="487" r="50" fill="url(#disc)" stroke="#fff" stroke-width="3"/>
    </g>
    <rect x="244" y="468" width="48" height="36" rx="2" fill="#bbb"/>
    <rect x="247" y="471" width="42" height="27" fill="#222"/>
    <path d="M264 477 L276 484.5 L264 492 Z" fill="#fff"/>
    <path d="M421 468 L436 484 L427 484 L427 505 L415 505 L415 484 L406 484 Z" fill="#5b93e0"/>
    <circle cx="573" cy="487" r="19" fill="#25a9e6"/>
    <text x="573" y="496" text-anchor="middle" font-family="Arimo, sans-serif" font-weight="700" font-size="24" fill="#fff">?</text>
    <g fill="none" stroke="#888" stroke-width="1.5">
      <path d="M326 490 Q345 500 362 488"/><path d="M354 485 L363 488 L358 496"/>
      <path d="M478 490 Q498 480 514 490"/><path d="M506 483 L515 490 L507 494"/>
    </g>
  </svg>

  <div class="hero-photo" role="img" aria-label="Photo of a gymnast in a black leotard performing a handstand split on the beam"></div>

  <p class="promo">Your Personal Gymnastic Judge!</p>
  <a class="cta-member">BECOME A MEMBER <i></i></a>

  <div class="floor"></div>
  <a class="blog-link"><span class="rss"></span><span>Read our Blog</span></a>
  <div class="social">
    <span aria-label="Social link"></span>
    <span aria-label="Social link"></span>
    <span aria-label="Social link"></span>
    <span aria-label="Email"><svg width="12" height="9" viewBox="0 0 12 9"><rect x=".5" y=".5" width="11" height="8" fill="none" stroke="#fff"/><path d="M.5 .5 L6 5 L11.5 .5" fill="none" stroke="#fff"/></svg></span>
  </div>

  <footer class="site-footer">Copyright ©&nbsp; 2012&nbsp; www.routineverdict.com &nbsp; All rights reserved.</footer>
</div>
</body>
</html>
```